business card

Business card for new business.
Red and black corporate colors.
Card can have an Indsutrial feel to it. Feel free to add Rust, Bolted steel, or graphics as you see fit. We provide highly specialized services to the below mentioned industries.
Keep information out of corners so that if I want I can choose rounded corners.
Information
- front. name - title - phone - email
- Rear
Refining - Rail - Infrastructure - Mining - Energy
Calgary - Edmonton - Fort McMurray - Revelstoke - Vancouver

```html
<!DOCTYPE html>
<html lang="en">
<head>
<meta charset="utf-8">
<title>Girderline Business Card</title>
<link href="https://fonts.googleapis.com/css2?family=Oswald:wght@500;600&family=Roboto:wght@400;700&display=swap" rel="stylesheet">
<style>
  :root {
    --bg: #5a4636;
    --card-black: #1c1d20;
    --card-black-light: #2a2b2f;
    --frame-gray: #8a8b8d;
    --steel-gray: #8f9092;
    --brand-red: #e30613;
    --red-deep: #c10010;
    --red-frame: #7d0010;
    --mark-dark: #3d0008;
    --list-ink: #3a070c;
    --white: #ffffff;
  }
  * { margin: 0; padding: 0; box-sizing: border-box; }
  html, body { width: 1200px; height: 960px; overflow: hidden; }
  body { background: var(--bg); position: relative; font-family: "Roboto", Arial, sans-serif; }

  .card { position: absolute; width: 600px; height: 340px; box-shadow: 0 3px 8px rgba(0,0,0,.45); }
  .card-front {
    left: 303px; top: 130px;
    background: radial-gradient(ellipse at 40% 40%, var(--card-black-light), var(--card-black) 70%);
  }
  .card-back {
    left: 300px; top: 488px; height: 342px;
    background: radial-gradient(ellipse at 50% 50%, var(--brand-red), var(--red-deep) 85%);
  }
  .card-frame { position: absolute; inset: 10px; border: 5px solid var(--frame-gray); }
  .card-back .card-frame { border-color: var(--red-frame); inset: 10px 10px 8px 10px; }

  .brand { position: absolute; left: 78px; top: 146px; display: flex; align-items: center; gap: 12px; }
  .brand-square { width: 16px; height: 16px; background: var(--brand-red); }
  .brand-name { font-family: "Oswald", Arial, sans-serif; font-weight: 600; font-size: 38px; color: var(--steel-gray); letter-spacing: .5px; line-height: 1; }

  .contact-block { position: absolute; left: 352px; top: 104px; }
  .person-name { font-family: "Oswald", Arial, sans-serif; font-weight: 600; font-size: 30px; color: var(--brand-red); line-height: 1; }
  .person-title { font-size: 18px; color: var(--steel-gray); margin-top: 4px; line-height: 1.1; }
  .contact-list { list-style: none; margin-top: 10px; }
  .contact-list li { display: flex; align-items: center; gap: 9px; font-size: 14px; color: var(--white); height: 19px; }
  .contact-list svg { width: 12px; height: 12px; fill: var(--brand-red); flex: none; }

  .mark-area { position: absolute; left: 167px; top: 88px; width: 109px; height: 182px; background: var(--mark-dark); }
  .service-list { position: absolute; left: 300px; top: 78px; list-style: none; }
  .service-list li { font-weight: 700; font-size: 14px; color: var(--list-ink); line-height: 19px; }
  .service-list li::before { content: "•"; margin-right: 6px; }
</style>
</head>
<body>
  <section class="card card-front">
    <div class="card-frame"></div>
    <div class="brand">
      <span class="brand-square"></span>
      <span class="brand-name">GIRDERLINE</span>
    </div>
    <div class="contact-block">
      <h1 class="person-name">DANIEL BROOKS</h1>
      <p class="person-title">CEO/FOUNDER</p>
      <ul class="contact-list">
        <li><svg viewBox="0 0 12 12"><path d="M2.5 0.5l2 2.5-1 1.3c.7 1.5 1.8 2.6 3.3 3.3l1.3-1 2.5 2-1.2 2.2C5 10.5 1.5 7 0.3 1.7z"/></svg>604 555 0192</li>
        <li><svg viewBox="0 0 12 12"><path d="M0 2h12v1L6 7 0 3z M0 4.5l6 4 6-4V10H0z"/></svg>info@girderline.com</li>
        <li><svg viewBox="0 0 12 12"><circle cx="6" cy="6" r="6"/><path d="M3 3.5h3v2H4zM7 7h2.5L8 9.5H6.5z" fill="#1c1d20"/></svg>www.girderline.com</li>
      </ul>
    </div>
  </section>

  <section class="card card-back">
    <div class="card-frame"></div>
    <div class="mark-area" role="img" aria-label="Brand mark area"></div>
    <ul class="service-list">
      <li>REFINING</li>
      <li>RAIL</li>
      <li>INFRASTRUCTURE</li>
      <li>MINING</li>
      <li>ENERGY</li>
      <li>CALGARY</li>
      <li>EDMONTON</li>
      <li>FORT MCMURRAY</li>
      <li>REVELSTOKE</li>
      <li>VANCOUVER</li>
    </ul>
  </section>
</body>
</html>
```